Dietitian needs awesome business card

I need a contemporary design that's eye catching but professional.
My card is to given to doctors, specialists and patients alike.
I manage patients with chronic diseases
I have uploaded my logo and current business card, I would also like the other Certified Clinical Nutritionist logo incorporated into the design

Target Market(s)

Doctors, specialists and patients

Industry/Entity Type

Healthcare

Contact Information for Business Card

www.brightfieldnutrition.com.au
Ph: 0427 561 903
Fax: 6457 2183
email: marcus.k.diet@fernmail.com
Space on the back of the card with: Appointment date, Appointment time and appointment location

Font styles to use
Serif

Colors
fbee3e
876aae
ffc214

Requirements
Must have
• My Logo
• Certified Clinical Nutritionist Logo
• My 4 locations - Pinebrook Medical Centre, North Corrin Health, Hollis Medical, Ashcombe Doctors Surgery
Nice to have
• I like the colours in my current business card

```html
<!DOCTYPE html>
<html lang="en">
<head>
<meta charset="utf-8">
<title>Brightfield Nutrition &amp; Dietetics – Business Card</title>
<link href="https://fonts.googleapis.com/css2?family=Source+Sans+3:ital,wght@0,400;0,600;1,400&display=swap" rel="stylesheet">
<style>
  :root {
    --backdrop: #2b2b2b;
    --navy: #1c2a86;
    --blue-mid: #1f52b8;
    --blue-glow: #0c86d8;
    --green: #5cb02e;
    --green-light: #9bd35a;
    --mint: #ebf5de;
    --ink: #2a3585;
    --rule: #8a93b8;
    --badge: #f07a22;
    --white: #ffffff;
  }
  * { margin: 0; padding: 0; box-sizing: border-box; }
  html, body {
    width: 1200px; height: 987px; overflow: hidden;
    background: var(--backdrop);
    font-family: "Source Sans 3", "Myriad Pro", sans-serif;
  }
  .card {
    position: absolute; width: 615px; height: 352px; overflow: hidden;
  }
  .card--front {
    left: 293px; top: 130px;
    background: radial-gradient(circle at 28% 38%, var(--blue-glow) 0%, var(--blue-mid) 35%, var(--navy) 80%);
  }
  .card--back { left: 292px; top: 505px; background: var(--mint); }

  .front-art { position: absolute; inset: 0; }
  .contact { position: absolute; left: 28px; top: 0; color: var(--white); }
  .contact__name { position: absolute; top: 70px; font-size: 23px; font-weight: 600; white-space: nowrap; }
  .contact__role { position: absolute; top: 99px; font-size: 16px; white-space: nowrap; }
  .contact__badge { position: absolute; top: 145px; width: 74px; height: 35px; background: var(--badge); border: 1px solid #f8a866; }
  .contact__lines { position: absolute; top: 200px; font-size: 16px; line-height: 23px; white-space: nowrap; }
  .contact__lines b { font-weight: 600; }

  .brand { position: absolute; left: 328px; top: 138px; display: flex; align-items: center; gap: 10px; color: var(--navy); font-weight: 400; }
  .brand__dot { width: 46px; height: 46px; border-radius: 50%; background: var(--navy); flex: none; }
  .brand__name { font-size: 30px; line-height: 1; }
  .brand__sub { font-size: 15px; line-height: 1.3; }

  .back-brand { position: absolute; left: 0; right: 0; top: 70px; display: flex; justify-content: center; align-items: center; gap: 10px; color: var(--ink); }
  .back-brand__dot { width: 40px; height: 40px; border-radius: 50%; background: var(--green); }
  .back-brand__name { font-size: 30px; }
  .web { position: absolute; left: 0; right: 0; top: 172px; text-align: center; font-style: italic; font-size: 17px; color: var(--ink); letter-spacing: .3px; }

  .field { position: absolute; color: var(--ink); font-size: 17px; white-space: nowrap; }
  .field--date { left: 41px; top: 240px; }
  .field--time { left: 353px; top: 240px; }
  .field--location { left: 41px; top: 292px; }
  .field--ampm { left: 529px; top: 244px; font-size: 13px; }
  .rule { position: absolute; height: 1px; background: var(--rule); }
  .rule--date { left: 95px; width: 250px; top: 262px; }
  .rule--time { left: 407px; width: 118px; top: 262px; }
  .rule--location { left: 125px; width: 448px; top: 313px; }
</style>
</head>
<body>
  <section class="card card--front">
    <svg class="front-art" width="615" height="352" viewBox="0 0 615 352">
      <defs>
        <radialGradient id="disc" cx="0.7" cy="0.35" r="0.7">
          <stop offset="0" stop-color="#ffffff"/>
          <stop offset="0.6" stop-color="#f4f7fb"/>
          <stop offset="1" stop-color="#e6edf6"/>
        </radialGradient>
      </defs>
      <circle cx="537" cy="182" r="256" fill="var(--green)"/>
      <circle cx="541" cy="180" r="249" fill="var(--white)"/>
      <circle cx="545" cy="178" r="244" fill="var(--green-light)"/>
      <circle cx="550" cy="176" r="238" fill="url(#disc)" role="img" aria-label="Soft faint leaf decoration in pale green and white"/>
    </svg>

    <div class="contact">
      <p class="contact__name">Marcus Kellaway</p>
      <p class="contact__role">Nutritionist &amp; Chef</p>
      <div class="contact__badge" role="img" aria-label="Certified Clinical Nutritionist badge"></div>
      <div class="contact__lines">
        <p><b>Phone :</b> 0427 561 903</p>
        <p><b>Fax :</b> 6457 2183</p>
        <p>marcus.k.diet@fernmail.com</p>
      </div>
    </div>

    <div class="brand">
      <span class="brand__dot"></span>
      <div>
        <p class="brand__name">Brightfield</p>
        <p class="brand__sub">Nutrition &amp; Dietetics</p>
      </div>
    </div>
  </section>

  <section class="card card--back">
    <div class="back-brand">
      <span class="back-brand__dot"></span>
      <span class="back-brand__name">Brightfield</span>
    </div>
    <p class="web">brightfieldnutrition.com.au</p>

    <span class="field field--date">Date :</span>
    <span class="rule rule--date"></span>
    <span class="field field--time">Time :</span>
    <span class="rule rule--time"></span>
    <span class="field field--ampm">AM/PM</span>
    <span class="field field--location">Location :</span>
    <span class="rule rule--location"></span>
  </section>
</body>
</html>
```